post card 4x6

this is a post card that will be sent to plumbing companies and foundation repair companies for whole sale work. if you can add ( work done in unmarked truck -will ware your shirt)

```html
<!DOCTYPE html>
<html lang="en">
<head>
<meta charset="utf-8">
<title>DrainView Wholesale Postcard</title>
<link href="https://fonts.googleapis.com/css2?family=Montserrat:wght@400;500;600;700;800;900&display=swap" rel="stylesheet">
<style>
  :root {
    --navy: #1d2738;
    --navy-deep: #141c2a;
    --red: #e8383d;
    --red-dark: #c72a2f;
    --grey: #8c929b;
    --light: #f4f4f4;
    --white: #ffffff;
    --text: #2a2f38;
    --page: #eceef1;
  }
  * { box-sizing: border-box; margin: 0; padding: 0; }
  html, body { width: 784px; height: 1200px; overflow: hidden; }
  body {
    background: var(--page);
    font-family: "Montserrat", Arial, sans-serif;
    position: relative;
  }
  .card {
    position: absolute;
    left: 42px;
    width: 700px;
    height: 467px;
    overflow: hidden;
    background: var(--white);
    box-shadow: 0 6px 18px rgba(0,0,0,.18);
  }
  .card--front { top: 80px; }
  .card--back { top: 607px; }

  /* FRONT */
  .front-hero {
    position: absolute; left: 0; top: 0; width: 700px; height: 272px;
    background: var(--navy);
  }
  .front-photo { position: absolute; left: 0; top: 0; }
  .brand {
    position: absolute;
    font-weight: 900;
    color: var(--red);
    letter-spacing: -0.5px;
    white-space: nowrap;
    display: flex; align-items: center; gap: 8px;
  }
  .brand__dot { width: 12px; height: 12px; background: var(--red); border-radius: 50%; flex: none; }
  .front-brand { left: 34px; top: 28px; font-size: 32px; }
  .headline { position: absolute; left: 34px; top: 86px; color: var(--white); line-height: 1; }
  .headline__lead { font-size: 27px; font-weight: 700; }
  .headline__mid { font-size: 35px; font-weight: 800; margin-top: 6px; }
  .headline__key { font-size: 48px; font-weight: 900; color: var(--red); margin-top: 4px; }
  .headline__sub { font-size: 14px; font-weight: 600; letter-spacing: .6px; margin-top: 8px; }

  .tagline-band {
    position: absolute; left: 0; top: 272px; width: 430px; height: 36px;
    background: var(--grey); color: var(--white);
    font-size: 14px; font-weight: 800; letter-spacing: .5px;
    display: flex; align-items: center; padding-left: 34px;
  }
  .service-grid {
    position: absolute; left: 34px; top: 324px;
    display: grid; grid-template-columns: 200px 220px; row-gap: 9px;
    list-style: none;
  }
  .service-grid li {
    font-size: 13px; font-weight: 600; color: var(--text);
    display: flex; align-items: center; gap: 8px; white-space: nowrap;
  }
  .service-grid li::before {
    content: ""; width: 8px; height: 8px; background: var(--red); flex: none;
  }
  .cta-bar {
    position: absolute; left: 0; bottom: 0; width: 700px; height: 58px;
    background: var(--navy); display: flex; align-items: stretch;
  }
  .cta-bar__label {
    width: 200px; color: var(--white); font-size: 12px; font-weight: 700;
    line-height: 1.3; padding: 13px 0 0 34px; letter-spacing: .4px;
  }
  .cta-bar__phone {
    width: 260px; background: var(--red); color: var(--white);
    font-size: 30px; font-weight: 800; display: flex; align-items: center; justify-content: center;
  }
  .cta-bar__web {
    flex: 1; color: var(--white); font-size: 12px; font-weight: 600;
    padding: 14px 0 0 22px; line-height: 1.5;
  }
  .cta-bar__web span { color: var(--red); font-weight: 700; }

  /* BACK */
  .back-panel { position: absolute; left: 0; top: 0; }
  .about { position: absolute; left: 30px; top: 30px; width: 250px; color: var(--white); }
  .section-title { font-size: 15px; font-weight: 800; letter-spacing: .5px; }
  .section-title em { font-style: normal; color: var(--red); }
  .about p { font-size: 10px; line-height: 1.55; margin-top: 9px; color: #d6d9de; }
  .about .section-title--services { margin-top: 22px; }
  .back-services { list-style: none; margin-top: 9px; }
  .back-services li {
    font-size: 11px; font-weight: 500; margin-bottom: 6px;
    display: flex; align-items: center; gap: 8px;
  }
  .back-services li::before { content: ""; width: 6px; height: 6px; background: var(--red); }
  .back-cta { position: absolute; left: 30px; bottom: 26px; color: var(--white); }
  .back-cta__label { font-size: 11px; font-weight: 700; letter-spacing: .4px; }
  .back-cta__phone {
    display: inline-block; margin-top: 6px; background: var(--red);
    font-size: 22px; font-weight: 800; padding: 4px 12px;
  }
  .back-cta__web { font-size: 11px; margin-top: 6px; }
  .back-brand { left: 392px; top: 44px; font-size: 28px; }
  .stamp {
    position: absolute; right: 26px; top: 24px; width: 62px; height: 72px;
    border: 2px dashed #b9bdc3;
  }
  .address-lines { position: absolute; left: 400px; top: 240px; width: 270px; }
  .address-lines span { display: block; height: 1px; background: #b9bdc3; margin-bottom: 34px; }
</style>
</head>
<body>

<section class="card card--front" aria-label="Postcard front">
  <div class="front-hero"></div>
  <svg class="front-photo" width="700" height="272" viewBox="0 0 700 272">
    <defs>
      <linearGradient id="pipeTones" x1="0" y1="0" x2="1" y2="1">
        <stop offset="0" stop-color="#cfd3d8"/>
        <stop offset="0.5" stop-color="#9aa1aa"/>
        <stop offset="1" stop-color="#6b6f76"/>
      </linearGradient>
    </defs>
    <polygon points="380,0 700,0 700,272 470,272" fill="var(--red)"/>
    <polygon points="396,0 700,0 700,258 484,258" fill="url(#pipeTones)" role="img" aria-label="Photo of a plumber fitting copper and steel pipes"/>
  </svg>
  <div class="brand front-brand"><span class="brand__dot"></span>DrainView</div>
  <div class="headline">
    <div class="headline__lead">Your One-Stop</div>
    <div class="headline__mid">SOLUTION FOR</div>
    <div class="headline__key">PLUMBING</div>
    <div class="headline__sub">AND IRRIGATION INSTALLATION</div>
  </div>
  <div class="tagline-band">YOU MAKE THE $ WE DO THE WORK</div>
  <ul class="service-grid">
    <li>Cipp (Cured In Place Pipe)</li>
    <li>Pipe Bursting</li>
    <li>Sipp (Spray In Place Pipe)</li>
    <li>Sewer Camera And Locate</li>
    <li>Hydro Jetting</li>
    <li>Descale Cast Iron</li>
  </ul>
  <div class="cta-bar">
    <div class="cta-bar__label">CALL FOR WHOLE<br>SALE PRICING</div>
    <div class="cta-bar__phone">555-014-2290</div>
    <div class="cta-bar__web">www.drainviewplumbing.com<br><span>LIC# 004512</span></div>
  </div>
</section>

<section class="card card--back" aria-label="Postcard back">
  <svg class="back-panel" width="700" height="467" viewBox="0 0 700 467">
    <polygon points="0,0 318,0 318,467 0,467" fill="var(--navy)"/>
    <polygon points="318,0 336,0 318,30" fill="var(--red)"/>
    <polygon points="330,110 372,110 418,160 372,210 330,210 376,160" fill="var(--red)"/>
    <polygon points="352,110 366,110 412,160 366,210 352,210 398,160" fill="var(--red-dark)"/>
    <rect x="318" y="452" width="382" height="15" fill="var(--red)"/>
  </svg>
  <div class="about">
    <div class="section-title">ABOUT <em>DRAINVIEW</em></div>
    <p>We are a licensed trenchless crew serving plumbing and foundation repair companies. Work done in unmarked truck — we will wear your shirt.</p>
    <div class="section-title section-title--services">OUR <em>SERVICES</em></div>
    <ul class="back-services">
      <li>Trenchless Pipe Repair</li>
      <li>Pipe Bursting</li>
      <li>Pipe Lining</li>
      <li>Sewer Video Inspection</li>
      <li>Hydro Jetting</li>
    </ul>
  </div>
  <div class="back-cta">
    <div class="back-cta__label">CALL FOR WHOLE SALE PRICING</div>
    <div class="back-cta__phone">555-014-2290</div>
    <div class="back-cta__web">www.drainviewplumbing.com</div>
  </div>
  <div class="brand back-brand"><span class="brand__dot"></span>DrainView</div>
  <div class="stamp"></div>
  <div class="address-lines"><span></span><span></span><span></span><span></span></div>
</section>

</body>
</html>
```